Business Card Design

We need a design for business cards for our company. We have a logo. We teach EMT's and we are based out of Virginia. The information that will need to add would be, name, title, phone number, email, address. On the back of the business card would be "Trained today, ready tomorrow"

Target Market(s)

People that want to become EMT's

Colors

Designer to choose colors to be used in the design.

Requirements
Must have
• company logo

```html
<!DOCTYPE html>
<html lang="en">
<head>
<meta charset="utf-8">
<title>Rescue Ready Academy – Business Card</title>
<link rel="stylesheet" href="https://fonts.googleapis.com/css2?family=Roboto:wght@400;500&display=swap">
<style>
  :root {
    --backdrop: #2b2b2b;
    --card-white: #ffffff;
    --brand-red: #be1e2d;
    --brand-grey: #939598;
    --ink: #2a2a2a;
    --rule: #8c8c8c;
  }
  * { margin: 0; padding: 0; box-sizing: border-box; }
  html, body { width: 1200px; height: 1200px; overflow: hidden; }
  body {
    background: var(--backdrop);
    position: relative;
    font-family: "Roboto", Arial, sans-serif;
  }
  .card {
    position: absolute;
    top: 310px;
    height: 594px;
  }
  .card-front {
    left: 234px;
    width: 364px;
    background: var(--card-white);
    text-align: center;
    color: var(--ink);
  }
  .brand-name {
    position: absolute;
    left: 0;
    right: 0;
    top: 152px;
    font-size: 27px;
    font-weight: 500;
    color: var(--brand-red);
    letter-spacing: 0.5px;
  }
  .contact {
    position: absolute;
    left: 0;
    right: 0;
    top: 382px;
  }
  .person-name {
    font-size: 22px;
    font-weight: 500;
    color: var(--brand-red);
    line-height: 22px;
  }
  .person-title {
    font-size: 17px;
    line-height: 20px;
  }
  .divider {
    width: 162px;
    height: 1px;
    background: var(--rule);
    margin: 10px auto 8px;
  }
  .contact-line {
    font-size: 17px;
    line-height: 22px;
  }
  .card-back {
    left: 627px;
    width: 369px;
    background: var(--brand-red);
    overflow: hidden;
  }
  .back-split { position: absolute; inset: 0; }
  .tagline {
    position: absolute;
    left: 0;
    right: 0;
    top: 527px;
    text-align: center;
    color: var(--card-white);
    font-family: Arial, Helvetica, sans-serif;
    font-size: 17px;
    letter-spacing: 0.6px;
  }
</style>
</head>
<body>
  <section class="card card-front">
    <div class="brand-name">Rescue Ready Academy</div>
    <div class="contact">
      <div class="person-name">DANIEL PORTER</div>
      <div class="person-title">Managing Director</div>
      <div class="divider"></div>
      <div class="contact-line">055-321 654 987</div>
      <div class="contact-line">hello@rescueready.com</div>
      <div class="divider"></div>
      <div class="contact-line">421, Address line goes here</div>
      <div class="contact-line">45452,Country Name</div>
    </div>
  </section>

  <section class="card card-back">
    <svg class="back-split" width="369" height="594" viewBox="0 0 369 594" aria-hidden="true">
      <path d="M0 0 H369 V370 C330 380 290 360 250 320 C190 260 110 220 60 215 C30 212 10 205 0 195 Z" fill="var(--brand-grey)"/>
    </svg>
    <div class="tagline">TRAINED TODAY, READY TOMORROW</div>
  </section>
</body>
</html>
```